Beacon Advisory Website

I currently have a website www.beaconadvisoryinc.com. We are a IT Consulting Company. Our website will pretty much tell out our services. I am looking to enhance my website and make it look more professional. Looking for very classy and Contemporary look and design for my website.

It Company

```html
<!DOCTYPE html>
<html lang="en">
<head>
<meta charset="utf-8">
<title>Beacon Advisory</title>
<link rel="stylesheet" href="https://fonts.googleapis.com/css2?family=Open+Sans:wght@400;600;700&family=Ubuntu:wght@400;500;700&display=swap">
<style>
:root{
  --blue:#1a6fb5;
  --blue-bright:#1c9ad6;
  --blue-deep:#0f5c9c;
  --ink:#333;
  --muted:#666;
  --grey-title:#6b6b6b;
  --section:#f0f0f0;
  --footer:#444;
  --footer-base:#333;
  --footer-text:#b9b9b9;
  --white:#fff;
}
*{margin:0;padding:0;box-sizing:border-box}
html,body{width:738px;height:1200px;overflow:hidden;background:var(--white)}
body{position:relative;font-family:"Open Sans",Arial,sans-serif;color:var(--ink)}
.abs{position:absolute}

/* hero */
.hero{left:0;top:0;width:738px;height:314px;background:linear-gradient(160deg,#d9d9d9 0%,#f4f4f4 40%,#bdbdbd 75%,#e6e6e6 100%)}
.site-header{left:0;top:0;width:738px;height:58px;background:rgba(255,255,255,.72)}
.brand{left:64px;top:18px;display:flex;align-items:center;gap:6px;font-family:"Ubuntu",sans-serif;font-weight:700;font-size:14px;color:var(--blue-deep)}
.brand-mark{width:14px;height:14px;background:var(--blue-deep)}
.nav{left:327px;top:22px;display:flex;align-items:center;font-size:8px;color:var(--blue-deep)}
.nav a{text-decoration:none;color:inherit;margin-right:16px}
.nav a.active{background:var(--blue-bright);color:var(--white);padding:5px 11px;margin-right:12px}
.nav svg{margin-left:12px}
.caption{left:422px;top:181px;width:255px;height:52px;background:rgba(30,30,30,.88);color:var(--white);padding:10px 12px}
.caption h1{font-family:"Ubuntu",sans-serif;font-size:13px;font-weight:500;letter-spacing:.3px}
.caption p{font-size:7.5px;margin-top:6px}

/* feature cards */
.card{top:340px;width:186px;height:153px}
.card-consult{left:71px;background:linear-gradient(180deg,#2f7fc4,#1a68ad);color:var(--white);padding:28px 23px}
.card-consult h2{font-family:"Ubuntu",sans-serif;font-weight:400;font-size:11px;display:flex;align-items:center;gap:10px}
.card-consult p{font-size:7px;line-height:13.5px;margin-top:10px;text-align:justify}
.card-consult .more{font-size:7px;color:var(--blue-bright);margin-top:4px}
.card-photo .shot{left:0;top:0;width:186px;height:120px}
.card-photo .bar{left:0;top:120px;width:186px;height:33px;background:var(--blue-deep);color:var(--white);font-family:"Ubuntu",sans-serif;font-size:11px;display:flex;align-items:center;padding-left:20px;gap:12px}

/* services */
.services{left:0;top:525px;width:738px;height:288px;background:var(--section)}
.section-title{width:738px;left:0;text-align:center;font-family:"Ubuntu",sans-serif;font-weight:700;font-size:20px;color:var(--grey-title)}
.section-title span{color:var(--blue-deep)}
.services .intro{left:130px;top:52px;width:478px;text-align:center;font-size:7px;line-height:13.5px;color:var(--ink)}
.svc{top:93px;width:144px;height:160px;background:var(--white);border:1px solid #dcdcdc;text-align:center;padding:16px 8px 0}
.svc h3{font-family:"Ubuntu",sans-serif;font-weight:400;font-size:11px;color:var(--blue-deep);margin-top:8px}
.svc p{font-size:7px;line-height:13.6px;color:var(--muted);margin-top:6px;text-align:justify;text-align-last:center}

/* testimonials */
.quote-photo{width:66px;height:66px;border-radius:50%;border:2px solid #e3e3e3;background:linear-gradient(160deg,#cfd6dc,#7c8791)}
.quote{width:155px;font-size:7px;line-height:13.6px;color:var(--ink);text-align:justify}
.quote .who{font-size:10px;color:var(--blue-bright);margin-top:5px;text-align:left}
.quote .role{font-size:7px;color:#aaa;text-align:left}
.pager{width:24px;height:24px;border-radius:50%;background:#e2e2e2;display:flex;align-items:center;justify-content:center}

/* footer */
.footer{left:0;top:1025px;width:738px;height:146px;background:var(--footer);color:var(--footer-text);font-size:7.5px}
.footer h4{font-family:"Open Sans",sans-serif;font-weight:600;font-size:9.5px;color:var(--white);margin-bottom:12px}
.footer .col{top:21px}
.footer li{list-style:none;line-height:17.5px}
.footer .line{display:flex;align-items:center;gap:8px;margin-top:8px}
.footer input{width:108px;height:20px;border:1px solid #666;background:transparent;font-size:6.5px;font-style:italic;color:#aaa;padding-left:6px;margin-top:10px;font-family:inherit}
.footer .btn{display:inline-block;background:var(--blue-deep);color:var(--white);font-size:7px;font-weight:700;padding:5px 7px;margin-top:11px}
.footer .social li{display:flex;align-items:center;gap:9px}
.footer .social i{display:block;width:9px;height:9px;border-radius:50%;background:var(--white)}
.base{left:0;top:1171px;width:738px;height:29px;background:var(--footer-base);color:var(--white);font-size:7px;text-align:center;line-height:29px}
</style>
</head>
<body>

<div class="abs hero" role="img" aria-label="Office desk photo with eyeglasses, reports and a laptop keyboard in grey tones"></div>
<header class="abs site-header"></header>
<div class="abs brand"><span class="brand-mark"></span>Beacon Advisory</div>
<nav class="abs nav">
  <a class="active">Home</a><a>Services</a><a>Solutions</a><a>Resources</a><a>Career</a><a>Contact Us</a>
  <svg width="9" height="9" viewBox="0 0 10 10"><circle cx="4" cy="4" r="3" fill="none" stroke="#0f5c9c" stroke-width="1.6"/><line x1="6.3" y1="6.3" x2="9" y2="9" stroke="#0f5c9c" stroke-width="1.8"/></svg>
</nav>
<div class="abs caption"><h1>TODAY’S IT MARKET IS A DYNAMIC</h1><p>We are a beacon advisory company</p></div>

<div class="abs card card-consult">
  <h2><svg width="18" height="16" viewBox="0 0 18 16"><circle cx="6" cy="4" r="3" fill="#5bb8ea"/><path d="M0 15c0-4 3-6 6-6s6 2 6 6z" fill="#5bb8ea"/><rect x="11" y="1" width="7" height="5" fill="#5bb8ea"/></svg>Consulting</h2>
  <p>Beacon Advisory has certified professional consultants to work with you to help increase the business by providing IT services ..</p>
  <div class="more">Read More &gt;&gt;</div>
</div>
<div class="abs card card-photo" style="left:277px">
  <div class="abs shot" role="img" aria-label="Photo of interlocking gears against a cloudy sky" style="background:linear-gradient(180deg,#c9d3dc,#8d949b)"></div>
  <div class="abs bar"><svg width="18" height="14" viewBox="0 0 18 14"><circle cx="5" cy="4" r="3" fill="#5bb8ea"/><circle cx="13" cy="4" r="3" fill="#5bb8ea"/><path d="M0 14c0-4 2-6 5-6s5 2 5 6zM8 14c0-4 2-6 5-6s5 2 5 6z" fill="#5bb8ea"/></svg>Staff Augmentation</div>
</div>
<div class="abs card card-photo" style="left:481px">
  <div class="abs shot" role="img" aria-label="Photo of an offshore drilling platform at sea" style="background:linear-gradient(180deg,#b6bfca,#7e8894 70%,#9aa4ae)"></div>
  <div class="abs bar"><svg width="14" height="18" viewBox="0 0 14 18"><path d="M7 0L3 14h8z" fill="none" stroke="#5bb8ea" stroke-width="1.4"/><rect x="0" y="14" width="14" height="4" fill="#5bb8ea"/></svg>Offshore</div>
</div>

<section class="abs services">
  <h2 class="abs section-title" style="top:20px">Our <span>Services</span></h2>
  <p class="abs intro">The Beacon Advisory Website Design team creates professional, High-Quality, good Looking and thought-provoking Web sites that stand out from your competition. Your website will be fully protected from hackers and viruses.</p>
  <div class="abs svc" style="left:60px">
    <svg width="28" height="28" viewBox="0 0 28 28"><circle cx="14" cy="14" r="5" fill="none" stroke="#0f5c9c" stroke-width="1.6"/><circle cx="14" cy="14" r="10" fill="none" stroke="#0f5c9c" stroke-width="1.6" stroke-dasharray="4 3"/></svg>
    <h3>Technology</h3><p>Beacon Advisory Training programs are perfect for individuals to enhance their careers. Our hands-on practical and interactive,....</p>
  </div>
  <div class="abs svc" style="left:218px">
    <svg width="28" height="28" viewBox="0 0 28 28" stroke="#0f5c9c" stroke-width="1.4"><line x1="14" y1="14" x2="14" y2="4"/><line x1="14" y1="14" x2="5" y2="11"/><line x1="14" y1="14" x2="23" y2="11"/><line x1="14" y1="14" x2="8" y2="23"/><line x1="14" y1="14" x2="21" y2="22"/><g fill="#0f5c9c" stroke="none"><circle cx="14" cy="14" r="3.5"/><circle cx="14" cy="4" r="2"/><circle cx="5" cy="11" r="2"/><circle cx="23" cy="11" r="2"/><circle cx="8" cy="23" r="2"/><circle cx="21" cy="22" r="2"/></g></svg>
    <h3>Business</h3><p>Our Offshore development model has a unique distinction of providing efficient software solutions with cost and quality advantage,...</p>
  </div>
  <div class="abs svc" style="left:376px">
    <svg width="28" height="28" viewBox="0 0 28 28"><rect x="2" y="4" width="24" height="16" fill="none" stroke="#0f5c9c" stroke-width="2"/><path d="M11 9l-3 3 3 3M17 9l3 3-3 3M15 8l-2 8" fill="none" stroke="#0f5c9c" stroke-width="1.3"/><rect x="10" y="22" width="8" height="2" fill="#0f5c9c"/></svg>
    <h3>Application Development</h3><p>Our team follows one of two approaches to development. In full lifecycle application projects, we assume complete,...</p>
  </div>
  <div class="abs svc" style="left:533px">
    <svg width="28" height="30" viewBox="0 0 28 30"><circle cx="11" cy="6" r="3.5" fill="#0f5c9c"/><path d="M6 20l2-10h6l2 10h-3v9h-4v-9z" fill="#0f5c9c"/><circle cx="21" cy="5" r="3" fill="none" stroke="#0f5c9c" stroke-width="1.4"/><circle cx="25" cy="10" r="2" fill="none" stroke="#0f5c9c" stroke-width="1.2"/></svg>
    <h3>Enterprise Integration</h3><p>As organizations work to achieve and sustain competitive advantage, the ability for IT departments to demonstrate,...</p>
  </div>
</section>

<h2 class="abs section-title" style="top:836px">What Our <span>Clients Say</span></h2>
<div class="abs quote-photo" style="left:102px;top:872px" role="img" aria-label="Client portrait photo"></div>
<div class="abs quote" style="left:186px;top:872px">
  <p>Lorem Ipsum is simply dummy text of the printing and typesetting industry. Lorem Ipsum has been the industry's standard dummy text ever since the 1500s,</p>
  <div class="who">Marissa Delaine,</div><div class="role">Financial Services Professional</div>
</div>
<div class="abs quote-photo" style="left:397px;top:872px" role="img" aria-label="Client portrait photo"></div>
<div class="abs quote" style="left:481px;top:872px">
  <p>Lorem Ipsum is simply dummy text of the printing and typesetting industry. Lorem Ipsum has been the industry's standard dummy text ever since the 1500s,</p>
  <div class="who">Teodora R. Valcourt,</div><div class="role">Financial Services Professional</div>
</div>
<div class="abs pager" style="left:332px;top:965px"><svg width="8" height="10" viewBox="0 0 8 10"><path d="M6 1L2 5l4 4" fill="none" stroke="#fff" stroke-width="2"/></svg></div>
<div class="abs pager" style="left:364px;top:965px"><svg width="8" height="10" viewBox="0 0 8 10"><path d="M2 1l4 4-4 4" fill="none" stroke="#fff" stroke-width="2"/></svg></div>

<footer class="abs footer">
  <div class="abs col" style="left:72px">
    <h4>Contact Us</h4>
    <p style="line-height:13px">Harbour Lane, Box: 2281,<br>Westmere NSW 2090</p>
    <div class="line" style="margin-top:12px"><svg width="10" height="10" viewBox="0 0 10 10"><path d="M2 1l2 2-1 1.5c.7 1.3 1.2 1.8 2.5 2.5L7 6l2 2-1.5 1.5C4.5 9 1 5.5.5 2.5z" fill="#1a6fb5"/></svg>+1 (555) 014 2290</div>
    <div class="line"><svg width="11" height="8" viewBox="0 0 11 8"><rect x=".5" y=".5" width="10" height="7" fill="none" stroke="#1a6fb5"/><path d="M.5.5l5 4 5-4" fill="none" stroke="#1a6fb5"/></svg>info@beaconadvisory.com</div>
  </div>
  <div class="abs col" style="left:266px">
    <h4>Solutions</h4>
    <ul><li>Dashboards</li><li>Data Warehousing</li><li>BPM</li><li>Contacts</li></ul>
  </div>
  <div class="abs col" style="left:408px">
    <h4>Newsletter sign up</h4>
    <p>Please sign up here for &nbsp;news</p>
    <input type="text" placeholder="Email address">
    <div><span class="btn">SUBSCRIBE</span></div>
  </div>
  <div class="abs col social" style="left:610px">
    <h4>Follow Us</h4>
    <ul><li><i></i>Linkwall</li><li><i></i>Chirper</li><li><i></i>Circles+</li></ul>
  </div>
</footer>
<div class="abs base">© 2016 Beacon Advisory &nbsp;All right reserved &nbsp;Term of Use</div>

</body>
</html>
```